Website Design Required

Our client needs a website built from scratch. The website is called Snap4Wall and is essentially a website that allows you to upload a photo, order and pay and your photo is printed onto a canvas. A closely related website is http://www.lumafold.co.za/ however this project needs a clean, fresh design that encourages purchases.

Snap4wall will be a dedicated website which allows users to upload and print a single image for large format printing.

The website flow will consist of the following:

• A landing page will be designed which showcases the product offering and offers simple and easy to understand instructions on how to get a photo up- loaded and delivered to their door.

• An upload page will exist that allows users the ability to upload a photo to the website for printing.

• Once the user has uploaded a photo the website will ensure that the dimensions are good enough for printing onto canvas and advise the user accordingly if it is not suitable.
• Once the photo has passed this validation we will take the user to a new page that will give them a preview of their photo. Here they will be given a chance to place the photo correctly should the need arise.

• Once the user is happy with the photo placement they will click on the next button which will take them to the payment and delivery page whereby they will need to complete all the fields.

• Once done, a final order page will appear confirming all the details of the order as well as payment and delivery information. Once the user is satisfied he can click the order button.

Requirements
Must have
• We will need the following pages designed:
1. Homepage
2. Upload page
3. Photo placement page (which allows users to align their photo onto the canvas)
4. Order & Payment page
Should not have
• The design should not use old style fonts and shoddy illustrations. If illustrations are used they have to be clean, simple, stylish.

```html
<!DOCTYPE html>
<html lang="en">
<head>
<meta charset="utf-8">
<title>Snap4Wall – Upload</title>
<link rel="stylesheet" href="https://fonts.googleapis.com/css2?family=Open+Sans:wght@400;600;700;800&display=swap">
<style>
:root{
  --bg:#000;
  --frame:#6d6d6d;
  --page:#fff;
  --sky:#a9d4db;
  --ink:#3e3e3e;
  --muted:#777;
  --faint:#b9b9b9;
  --accent:#2e9ee0;
  --link:#3a8fd8;
  --nav-top:#ffffff;
  --nav-bot:#e4e4e4;
  --tab:#6a6a6a;
  --red:#d8432c;
  --sheet:#dcdcdc;
  --wood:#c8975a;
  --green:#3aa83a;
}
*{box-sizing:border-box;margin:0;padding:0}
html,body{width:1024px;height:1200px;overflow:hidden;background:var(--bg);font-family:"Open Sans",Arial,sans-serif;color:var(--ink)}
.canvas{position:relative;width:1024px;height:1200px}
.abs{position:absolute}
.smoke{top:60px;width:90px;height:680px;background:radial-gradient(ellipse at center,rgba(200,200,200,.35),rgba(0,0,0,0) 70%)}
.smoke.left{left:0}.smoke.right{right:0}
.frame{left:86px;top:24px;width:848px;height:1152px;background:var(--frame);border:2px solid #fff}
.page{left:100px;top:50px;width:818px;height:1100px;background:linear-gradient(var(--sky),var(--page) 360px)}
.nav{left:136px;top:70px;width:740px;height:38px;border-radius:6px;background:linear-gradient(var(--nav-top),var(--nav-bot));border:1px solid #c9c9c9}
.nav-item{top:78px;font-size:17px;color:#333;transform:translateX(-50%)}
.nav-sep{top:76px;width:1px;height:28px;background:#cfcfcf}
.tab-home{left:145px;top:64px;width:116px;height:46px;border-radius:8px 8px 10px 10px;background:linear-gradient(#8a8a8a,var(--tab));color:#fff;font-size:17px;text-align:center;line-height:50px;box-shadow:0 2px 3px rgba(0,0,0,.4)}
.brand{left:277px;top:48px;width:110px;height:175px;background:#000;border:6px solid #fff;box-shadow:0 2px 5px rgba(0,0,0,.4);color:#fff;font-size:17px;font-weight:600;display:flex;align-items:center;justify-content:center;flex-direction:column;gap:6px}
.brand .dot{width:10px;height:10px;background:#fff}
.step-icon{left:565px;top:132px;width:58px;height:52px;transform:rotate(-14deg);background:linear-gradient(#4b9be0 0,#8fc7f0 50%,#5eb43f 52%,#3f8f2c);border:4px solid #fff;box-shadow:0 2px 4px rgba(0,0,0,.3)}
.step-title{left:637px;top:126px;font-size:27px;font-weight:700;color:#444;letter-spacing:-.5px}
.step-sub{left:637px;top:156px;font-size:17px;color:#666}
.step-num{left:784px;top:128px;font-size:44px;font-weight:700;color:#444}
.content{left:135px;top:188px;width:743px;height:890px;background:#fff;border:3px solid #8a8a8a}
.steps{left:147px;width:447px;height:47px}
.steps svg{position:absolute;left:0;top:0}
.s-num{font-size:30px;font-weight:700;color:var(--faint);top:2px}
.s-lbl{font-size:12px;font-weight:700;color:var(--faint);top:11px;line-height:1}
.s-lbl small{display:block;font-size:8px;font-weight:400;margin-top:2px;color:#c8c8c8}
.on .s-num{color:#333}.on.s-lbl{color:var(--accent)}.on.s-lbl small{color:#222}
.ph{background:linear-gradient(135deg,#d5d5d5,#3a3a3a 55%,#bdbdbd)}
.intro{left:383px;top:314px;font-size:13px;line-height:16px;color:#222}
.intro a{color:var(--link);text-decoration:none}
.btn{border-radius:8px;background:linear-gradient(#f6f6f1,#c9c9bd);border:1px solid #aaa;box-shadow:0 1px 2px rgba(0,0,0,.3);color:#333;display:flex;align-items:center}
.btn-upload{left:383px;top:387px;width:176px;height:36px;font-size:18px;padding-left:9px}
.sec-title{font-size:16px;font-weight:700;color:#444}
.radio{width:9px;height:9px;border-radius:50%;border:1px solid #999;background:radial-gradient(#888 30%,#eee 40%)}
.row{font-size:10px;font-weight:700;color:#333}
.sheet{border:3px solid var(--red);background:linear-gradient(135deg,#eee,var(--sheet));box-shadow:2px 2px 2px rgba(0,0,0,.25);font-size:13px;font-weight:700;color:#333;text-align:right;padding-right:6px}
.wood{background:linear-gradient(90deg,#a9773e,var(--wood),#e0b880)}
.btn-next{left:437px;top:1012px;width:159px;height:40px;font-size:17px;font-weight:700;padding-left:14px}
.card{top:1098px;width:34px;height:24px;border:1px solid #bbb;border-radius:2px;font-size:8px;font-weight:700;color:#555;text-align:center;line-height:22px;background:#f2f2f2}
.legal{left:514px;top:1130px;transform:translateX(-50%);font-size:9px;color:#222;white-space:nowrap}
</style>
</head>
<body>
<div class="canvas">
  <div class="abs smoke left" role="img" aria-label="Soft smoke swirl background"></div>
  <div class="abs smoke right" role="img" aria-label="Soft smoke swirl background"></div>
  <div class="abs frame"></div>
  <div class="abs page"></div>

  <nav>
    <div class="abs nav"></div>
    <div class="abs tab-home">Home</div>
    <div class="abs nav-sep" style="left:537px"></div>
    <div class="abs nav-sep" style="left:648px"></div>
    <div class="abs nav-sep" style="left:765px"></div>
    <span class="abs nav-item" style="left:461px">Canvas Options</span>
    <span class="abs nav-item" style="left:590px">Pricing</span>
    <span class="abs nav-item" style="left:708px">Blog</span>
    <span class="abs nav-item" style="left:822px">Contact</span>
    <div class="abs brand"><span class="dot"></span>Snap4Wall</div>
  </nav>

  <div class="abs step-icon" role="img" aria-label="Small photo print icon"></div>
  <div class="abs step-title">UPLOAD</div>
  <div class="abs step-sub">Select your photo</div>
  <div class="abs step-num">1</div>

  <div class="abs content"></div>

  <!-- step bar 1 -->
  <div class="abs steps" style="top:236px">
    <svg width="447" height="47"><rect x=".5" y=".5" width="446" height="46" rx="3" fill="#f7f7f7" stroke="#d4d4d4"/><path d="M1 1H285L297 23.5L285 46H1Z" fill="#fff"/><path d="M285 1L297 23.5L285 46M435 1L447 23.5L435 46" fill="none" stroke="#d4d4d4"/></svg>
    <span class="abs s-num" style="left:13px;color:#333">1</span>
    <span class="abs s-lbl on" style="left:40px">CHOOSE PHOTO<small>Upload a photo</small></span>
    <span class="abs s-num" style="left:158px">2</span>
    <span class="abs s-lbl" style="left:190px">SIZE IT<small>Select your size</small></span>
    <span class="abs s-num" style="left:308px">3</span>
    <span class="abs s-lbl" style="left:336px">FRAME IT<small>Select your frame</small></span>
  </div>

  <div class="abs ph" style="left:175px;top:305px;width:155px;height:140px;border-radius:8px" role="img" aria-label="Illustration of a classic rangefinder camera"></div>
  <p class="abs intro">Now, click on the Upload Photo button and select your photo.<br>If your photo does not appear on the right, please <a href="#">click here and try again</a>.</p>
  <div class="abs btn btn-upload">Upload Now
    <svg width="48" height="34" viewBox="0 0 48 34" style="margin-left:6px"><path d="M14 2H34V14H44L24 33L4 14H14Z" fill="var(--green)"/></svg>
  </div>

  <!-- step bar 2 -->
  <div class="abs steps" style="top:466px">
    <svg width="447" height="47"><rect x=".5" y=".5" width="446" height="46" rx="3" fill="#f7f7f7" stroke="#d4d4d4"/><path d="M285 1L297 23.5L285 46H435L447 23.5L435 1Z" fill="#fff"/><path d="M285 1L297 23.5L285 46M435 1L447 23.5L435 46" fill="none" stroke="#d4d4d4"/></svg>
    <span class="abs s-num" style="left:13px">1</span>
    <span class="abs s-lbl" style="left:40px">CHOOSE PHOTO<small>Upload a photo</small></span>
    <span class="abs s-num" style="left:158px;color:#333">2</span>
    <span class="abs s-lbl on" style="left:190px">SIZE IT<small>Select your size</small></span>
    <span class="abs s-num" style="left:308px">3</span>
    <span class="abs s-lbl" style="left:336px">FRAME IT<small>Select your frame</small></span>
  </div>

  <h2 class="abs sec-title" style="left:170px;top:538px">SELECT YOUR SIZE</h2>
  <div class="abs radio" style="left:167px;top:581px"></div><span class="abs row" style="left:200px;top:578px">A4</span><span class="abs row" style="left:277px;top:578px">R100</span>
  <div class="abs radio" style="left:167px;top:613px"></div><span class="abs row" style="left:200px;top:610px">A3</span><span class="abs row" style="left:277px;top:610px">R120</span>
  <div class="abs radio" style="left:167px;top:643px"></div><span class="abs row" style="left:200px;top:640px">A2</span><span class="abs row" style="left:277px;top:640px">R140</span>
  <div class="abs radio" style="left:167px;top:673px"></div><span class="abs row" style="left:200px;top:670px">A1</span><span class="abs row" style="left:277px;top:670px">R150</span>
  <div class="abs radio" style="left:167px;top:703px"></div><span class="abs row" style="left:200px;top:700px">70 X 100</span><span class="abs row" style="left:277px;top:700px">R160</span>

  <div class="abs sheet" style="left:649px;top:537px;width:138px;height:175px">70 x 100</div>
  <div class="abs sheet" style="left:618px;top:563px;width:120px;height:149px">A1</div>
  <div class="abs sheet" style="left:585px;top:585px;width:104px;height:127px">50 x 70</div>
  <div class="abs sheet" style="left:554px;top:603px;width:88px;height:109px">A2</div>
  <div class="abs sheet" style="left:537px;top:632px;width:62px;height:80px">A3</div>
  <div class="abs sheet" style="left:521px;top:654px;width:48px;height:58px;text-align:left;padding-left:4px">A4</div>

  <!-- step bar 3 -->
  <div class="abs steps" style="top:736px">
    <svg width="447" height="47"><rect x=".5" y=".5" width="446" height="46" rx="3" fill="#f7f7f7" stroke="#d4d4d4"/><path d="M435 1L447 23.5L435 46H446V1Z" fill="#fff"/><path d="M285 1L297 23.5L285 46M435 1L447 23.5L435 46" fill="none" stroke="#d4d4d4"/></svg>
    <span class="abs s-num" style="left:13px">1</span>
    <span class="abs s-lbl" style="left:40px">CHOOSE PHOTO<small>Upload a photo</small></span>
    <span class="abs s-num" style="left:158px">2</span>
    <span class="abs s-lbl" style="left:190px">SIZE IT<small>Select your size</small></span>
    <span class="abs s-num" style="left:308px;color:#333">3</span>
    <span class="abs s-lbl on" style="left:336px">FRAME IT<small>Select your frame</small></span>
  </div>

  <h2 class="abs sec-title" style="left:170px;top:804px">SELECT YOUR FRAME</h2>
  <div class="abs wood" style="left:192px;top:841px;width:124px;height:101px;clip-path:polygon(0 0,100% 0,100% 15%,17% 15%,17% 100%,0 100%)" role="img" aria-label="Corner sample of a light oak frame"></div>
  <div class="abs wood" style="left:378px;top:840px;width:147px;height:100px;clip-path:polygon(0 0,100% 0,100% 24%,17% 24%,17% 100%,0 100%)" role="img" aria-label="Corner sample of a moulded pine frame"></div>
  <div class="abs radio" style="left:197px;top:962px"></div><span class="abs row" style="left:223px;top:961px">Select this frame</span>
  <div class="abs radio" style="left:387px;top:962px"></div><span class="abs row" style="left:413px;top:961px">Select this frame</span>

  <div class="abs btn btn-next">NEXT STEP
    <svg width="40" height="36" viewBox="0 0 40 36" style="margin-left:8px"><path d="M4 10H18V1L36 18L18 35V26H4Z" fill="#9fd3e6"/></svg>
  </div>

  <footer>
    <div class="abs card" style="left:430px">Cardo</div>
    <div class="abs card" style="left:474px">Axis</div>
    <div class="abs card" style="left:515px">PayLink</div>
    <div class="abs card" style="left:557px">Nova</div>
    <div class="abs legal">Terms &amp; Conditions | Privacy Policy</div>
  </footer>
</div>
</body>
</html>
```